Alaska Law Firm Needs a Sticker Design

We need a design for stickers to put on already-printed brochures. We mail the brochures to potential clients so they can learn more about accident-induced injuries, insurance claims, legal representation, and our own law firm.

One of our lawyers wrote a book that provides a helpful overview of personal injury claims. We are offering this book for free to anyone who calls and requests it. Therefore, the sticker design should include one of the following phrases, or something very similar:
a) "Still have questions? Call and request our book-- for free!"
b) "Still have questions about auto accident claims? Call and request our book today."
c) "Still have questions about filing a claim? Call and request a free copy of our book."
d) "Still have questions? Call us today to request a free copy of our book, Clear Lanes Ahead."
e) "To learn more about automobile accidents and insurance, call today and request a free copy of our book."

The sticker should be approximately 3"x3" and may be a circle, square, rectangle, or ellipsis. The sticker will be placed on the back of the folder, which is light blue. We would like the sticker to match the color scheme of our website and the folder.

I will upload an image of the book cover as soon as I obtain it.

Law Firm

Font styles to use
Serif
Sans Serif

Requirements
Should not have
• Bright colors that aren't already used in the folder design. e.g. no bright orange, pink, chartreuse, turquoise, yellow, red.

```html
<!DOCTYPE html>
<html lang="en">
<head>
<meta charset="utf-8">
<title>Free Book Sticker</title>
<link rel="stylesheet" href="https://fonts.googleapis.com/css2?family=Ubuntu:wght@400;500;700&display=swap">
<style>
  :root {
    --bg-light: #f4f4f4;
    --bg-dark: #d6d6d6;
    --sky-core: #b9dcf4;
    --sky-edge: #7db6e0;
    --navy: #0b3a66;
    --ink-navy: #123d66;
    --ink-gray: #4e5862;
    --ink-black: #111111;
    --ring-gray: #5d5d5d;
    --ring-white: #ffffff;
  }
  html, body {
    margin: 0;
    padding: 0;
    width: 1200px;
    height: 1200px;
    overflow: hidden;
  }
  body {
    background: radial-gradient(circle at 50% 45%, var(--bg-light), var(--bg-dark));
    font-family: "Ubuntu", "Trebuchet MS", sans-serif;
  }
  .sticker {
    display: block;
    width: 1200px;
    height: 1200px;
  }
  .sticker text { font-family: "Ubuntu", "Trebuchet MS", sans-serif; }
  .ink-navy { fill: var(--ink-navy); }
  .ink-gray { fill: var(--ink-gray); }
  .ink-black { fill: var(--ink-black); }
  .ink-white { fill: #ffffff; }
  .w-regular { font-weight: 400; }
  .w-medium { font-weight: 500; }
  .w-bold { font-weight: 700; }
  .caller-part { fill: var(--navy); }
  .caller-head { stroke: var(--sky-edge); stroke-width: 3; }
  .handset { fill: var(--navy); stroke: var(--sky-core); stroke-width: 0.6; }
</style>
</head>
<body>
<svg class="sticker" viewBox="0 0 1200 1200" xmlns="http://www.w3.org/2000/svg" aria-label="Free book offer sticker">
  <defs>
    <radialGradient id="skyFill" cx="55%" cy="55%" r="60%">
      <stop offset="0%" stop-color="var(--sky-core)"/>
      <stop offset="100%" stop-color="var(--sky-edge)"/>
    </radialGradient>
  </defs>

  <g transform="translate(600 600) scale(1.35) translate(-735 -410)">
    <!-- layered rings -->
    <circle cx="722" cy="388" r="312" fill="var(--ring-gray)"/>
    <circle cx="760" cy="412" r="310" fill="var(--navy)"/>
    <circle cx="708" cy="435" r="312" fill="var(--ring-white)"/>
    <circle class="sticker-face" cx="735" cy="410" r="310" fill="url(#skyFill)"/>

    <!-- call badge: caller silhouette with handset -->
    <g class="call-badge" role="img" aria-label="Caller icon holding a phone handset">
      <path class="caller-part" d="M488 512 L488 474 Q492 446 528 440 L556 440 Q594 446 598 474 L598 512 Z"/>
      <ellipse class="caller-part caller-head" cx="541" cy="413" rx="34" ry="38"/>
      <g transform="translate(470 402) rotate(8) scale(2.9)">
        <path class="handset" d="M6.62 10.79c1.44 2.83 3.76 5.14 6.59 6.59l2.2-2.2c.27-.27.67-.36 1.02-.24 1.12.37 2.33.57 3.57.57.55 0 1 .45 1 1V20c0 .55-.45 1-1 1-9.39 0-17-7.61-17-17 0-.55.45-1 1-1h3.5c.55 0 1 .45 1 1 0 1.25.2 2.45.57 3.57.11.35.03.74-.25 1.02l-2.2 2.2z"/>
      </g>
      <text class="ink-white w-regular" x="518" y="505" font-size="38" textLength="66" lengthAdjust="spacingAndGlyphs">call</text>
    </g>

    <!-- message -->
    <text class="ink-navy w-regular" x="560" y="248" font-size="48" textLength="190" lengthAdjust="spacingAndGlyphs">"To learn</text>
    <text class="ink-navy w-bold" x="758" y="248" font-size="62" textLength="157" lengthAdjust="spacingAndGlyphs">more</text>

    <text class="ink-navy w-bold" x="520" y="305" font-size="62" textLength="172" lengthAdjust="spacingAndGlyphs">about</text>
    <text class="ink-gray w-regular" x="704" y="303" font-size="44" textLength="218" lengthAdjust="spacingAndGlyphs">automobile</text>

    <text class="ink-black w-medium" x="510" y="366" font-size="74" textLength="336" lengthAdjust="spacingAndGlyphs">accidents</text>
    <text class="ink-navy w-regular" x="857" y="355" font-size="44" textLength="72" lengthAdjust="spacingAndGlyphs">and</text>

    <text class="ink-navy w-medium" x="592" y="432" font-size="74" textLength="368" lengthAdjust="spacingAndGlyphs">insurance,</text>

    <text class="ink-black w-regular" x="600" y="482" font-size="44" textLength="119" lengthAdjust="spacingAndGlyphs">today</text>
    <text class="ink-gray w-regular" x="728" y="482" font-size="44" textLength="234" lengthAdjust="spacingAndGlyphs">and request</text>

    <text class="ink-gray w-medium" x="607" y="540" font-size="52" textLength="282" lengthAdjust="spacingAndGlyphs">a free copy</text>

    <text class="ink-navy w-bold" x="520" y="606" font-size="68" textLength="438" lengthAdjust="spacingAndGlyphs">of our book."</text>
  </g>
</svg>
</body>
</html>
```